professional business card design

Business card design. Photos have been uploaded and i am open to the designer choosing which photos to use. Would like the card to be mostyly in a grey scale design with black, whites, silver & grey colours. I have added copy of our flyer as would like on the back side of card our services to be listed. Do not use any bright colurs such as blue red green or yellow. i need to be able to edit the phone number and naem in the final card design submitted.

Target Market(s)

Clients

Industry/Entity Type

earhmovibng and transport

Contact Information for Business Card

Director Name, address, email, phone number and services

Colors

Designer to choose only greyscale colors for use in the design.

Requirements
Should not have
• no yellow, red, blue or green

```html
<!DOCTYPE html>
<html lang="en">
<head>
<meta charset="utf-8">
<title>Dunmore Haul – Business Card</title>
<link rel="stylesheet" href="https://fonts.googleapis.com/css2?family=Roboto:wght@400;500;700&family=Michroma&display=swap">
<style>
  :root {
    --page: #d9d9d9;
    --card-dark: #0b0b0b;
    --card-dark-mid: #2a2a2a;
    --metal-light: #cfcfcf;
    --metal: #9a9a9a;
    --card-light: #d3d3d3;
    --ink: #2b2b2b;
    --ink-soft: #3a3a3a;
    --white: #f2f2f2;
  }
  * { box-sizing: border-box; margin: 0; padding: 0; }
  html, body { width: 1159px; height: 1200px; overflow: hidden; }
  body {
    background: var(--page);
    font-family: "Roboto", Arial, sans-serif;
    position: relative;
  }
  .card {
    position: absolute;
    left: 303px;
    width: 553px;
    height: 316px;
    border-radius: 8px;
    overflow: hidden;
  }

  /* ---------- Back side: services ---------- */
  .card-services {
    top: 250px;
    background:
      linear-gradient(90deg, #000 0%, #000 10%, transparent 16%, transparent 84%, #000 90%, #000 100%),
      radial-gradient(ellipse at 50% 40%, #5a5a5a 0%, var(--card-dark-mid) 45%, var(--card-dark) 80%);
    color: var(--white);
  }
  .card-services .brand {
    position: absolute;
    top: 36px;
    width: 100%;
    text-align: center;
    font-family: "Roboto", Arial, sans-serif;
    font-weight: 700;
    font-size: 54px;
    letter-spacing: 2px;
    color: var(--metal-light);
    line-height: 1;
  }
  .card-services .brand-suffix {
    position: absolute;
    top: 108px;
    width: 100%;
    text-align: center;
    font-weight: 700;
    font-size: 15px;
    color: var(--metal);
  }
  .fleet-photo {
    position: absolute;
    left: 0;
    top: 144px;
    width: 100%;
    height: 74px;
    background: linear-gradient(180deg, #2c2c2c 0%, #6e6e6e 45%, #3a3a3a 75%, #1a1a1a 100%);
  }
  .services-title {
    position: absolute;
    left: 27px;
    top: 219px;
    font-family: "Michroma", Arial, sans-serif;
    font-size: 15px;
    letter-spacing: 0.5px;
    color: var(--white);
  }
  .services-list {
    position: absolute;
    left: 27px;
    top: 246px;
    width: 510px;
    list-style: none;
    display: grid;
    grid-template-columns: 196px 1fr;
    row-gap: 2px;
    font-family: "Michroma", Arial, sans-serif;
    font-size: 7px;
    line-height: 9.5px;
    color: var(--white);
    font-variant: small-caps;
  }
  .services-list li::before {
    content: "";
    display: inline-block;
    width: 5px;
    height: 6px;
    border: 1px solid var(--white);
    border-radius: 1px;
    margin-right: 4px;
    vertical-align: -1px;
  }
  .services-list .wide { grid-column: 1 / 3; }

  /* ---------- Front side: contact ---------- */
  .card-contact {
    top: 634px;
    background: var(--card-light);
    color: var(--ink);
  }
  .person-name {
    position: absolute;
    left: 42px;
    top: 45px;
    font-weight: 700;
    font-size: 24px;
    letter-spacing: 0.3px;
  }
  .person-role {
    position: absolute;
    left: 42px;
    top: 74px;
    font-weight: 500;
    font-size: 12px;
    letter-spacing: 0.3px;
    color: var(--ink-soft);
  }
  .rule {
    position: absolute;
    left: 209px;
    top: 82px;
    width: 304px;
    height: 2px;
    background: var(--ink);
  }
  .card-contact .brand {
    position: absolute;
    right: 40px;
    top: 44px;
    font-weight: 700;
    font-size: 22px;
    letter-spacing: 1px;
    color: var(--ink);
  }
  .address, .contact-lines {
    position: absolute;
    bottom: 27px;
    font-size: 15.5px;
    line-height: 22px;
    color: var(--ink-soft);
  }
  .address { left: 41px; }
  .contact-lines { right: 40px; text-align: right; }
</style>
</head>
<body>

<section class="card card-services">
  <div class="brand">DUNMORE</div>
  <div class="brand-suffix">Pty Ltd</div>
  <div class="fleet-photo" role="img" aria-label="Photo of a road train fleet of tipper trailers lined up"></div>
  <h2 class="services-title">OUR SERVICES</h2>
  <ul class="services-list">
    <li>Over size loads/ Hot Shot Loads</li>
    <li>Heavy Vehicle Recovery Services</li>
    <li>Potable Water Deliveries</li>
    <li>Road Building / Maintenance</li>
    <li>Sand &amp; Metal Supply &amp; Cartage:</li>
    <li>Road Train Tippers</li>
    <li>Road Train Tankers</li>
    <li>Road Train Flat Tops</li>
    <li class="wide">Mine Site accredited equipment &amp; Operators</li>
  </ul>
</section>

<section class="card card-contact">
  <h1 class="person-name">MARTEN HALE</h1>
  <p class="person-role">GRAPHIC DESIGNER &amp; CEO</p>
  <div class="rule"></div>
  <div class="brand">DUNMORE</div>
  <p class="address">48 Quarry Road, Ironvale</p>
  <p class="contact-lines">
    0098 7654 32110<br>
    office@dunmorehaul.com<br>
    dunmorehaul.com
  </p>
</section>

</body>
</html>
```